Simple and clean

We need a business card design for a new company called Dwelling Hawk. It is a search engine to find current properties for sale or rent in New Zealand market.
We have already a colour scheme that we would like people to use.
Light brown: #D4CCB0
Light green: #D6E4D4
Green: #669966
Black/White
It is OK to divert from this colour scheme slightly as long as there is a green component to the business card.
Final design should be clean, simple and should communicate the nature of the business.
Target Market(s)
- First home buyers
- Real estate agents
- People seeking rentals
Industry/Entity Type
Business
Requirements
Must have
- Use those or similar colours.
Light brown: #D4CCB0
Light green: #D6E4D4
Green: #669966
Black/White

```html
<!DOCTYPE html>
<html lang="en">
<head>
<meta charset="utf-8">
<title>Dwelling Hawk – Business Card</title>
<link rel="stylesheet" href="https://fonts.googleapis.com/css2?family=Open+Sans:wght@600;700&family=Arimo:wght@400&display=swap">
<style>
  :root {
    --page-bg: #ffffff;
    --card-black: #050505;
    --card-charcoal: #161616;
    --brand-brown: #D4CCB0;
    --brand-brown-light: #E3DDC8;
    --brand-green-light: #D6E4D4;
    --brand-green: #669966;
    --text-white: #ffffff;
  }
  * { margin: 0; padding: 0; box-sizing: border-box; }
  html, body {
    width: 1200px;
    height: 900px;
    overflow: hidden;
    background: var(--page-bg);
  }
  .canvas {
    position: relative;
    width: 1200px;
    height: 900px;
  }
  .business-card {
    position: absolute;
    left: 150px;
    top: 180px;
    width: 900px;
    height: 540px;
    background: var(--card-black);
    overflow: hidden;
  }
  .card-wave {
    position: absolute;
    inset: 0;
    width: 100%;
    height: 100%;
  }
  .brand {
    position: absolute;
    left: 48px;
    top: 40px;
    display: flex;
    align-items: center;
    gap: 20px;
  }
  .brand-dot {
    width: 46px;
    height: 46px;
    border-radius: 50%;
    background: var(--brand-green);
  }
  .brand-name {
    font-family: "Open Sans", sans-serif;
    font-weight: 700;
    font-size: 84px;
    line-height: 1;
    letter-spacing: -1px;
    color: var(--brand-green-light);
  }
  .contact {
    position: absolute;
    left: 52px;
    top: 232px;
  }
  .contact-name,
  .contact-role {
    font-family: "Open Sans", sans-serif;
    font-weight: 600;
    font-size: 30px;
    line-height: 1;
    color: var(--brand-green);
  }
  .contact-details {
    margin-top: 30px;
    font-family: "Arimo", Arial, sans-serif;
    font-size: 26px;
    line-height: 1.05;
    color: var(--text-white);
  }
  .contact-web {
    margin-top: 24px;
    font-family: "Arimo", Arial, sans-serif;
    font-size: 26px;
    color: var(--text-white);
  }
  .card-band {
    position: absolute;
    left: 0;
    right: 0;
    bottom: 0;
    height: 84px;
    background: var(--brand-brown);
    border-top: 10px solid var(--brand-brown-light);
    display: flex;
    align-items: center;
    justify-content: center;
    padding-left: 180px;
  }
  .band-web {
    font-family: "Open Sans", sans-serif;
    font-weight: 600;
    font-size: 22px;
    letter-spacing: 0.32em;
    color: var(--brand-green);
  }
</style>
</head>
<body>
  <main class="canvas">
    <section class="business-card">
      <svg class="card-wave" viewBox="0 0 900 540" preserveAspectRatio="none" aria-hidden="true">
        <path d="M0 190 C 180 150, 360 150, 520 200 S 780 300, 900 270 L 900 540 L 0 540 Z" fill="var(--card-charcoal)"/>
      </svg>

      <div class="brand">
        <span class="brand-dot"></span>
        <span class="brand-name">Dwelling Hawk</span>
      </div>

      <div class="contact">
        <p class="contact-name">Alex Morgan</p>
        <p class="contact-role">Director</p>
        <p class="contact-details">Mobile number<br>Email address</p>
        <p class="contact-web">www.dwellinghawk.co.nz</p>
      </div>

      <footer class="card-band">
        <span class="band-web">www.dwellinghawk.co.nz</span>
      </footer>
    </section>
  </main>
</body>
</html>
```